Landing Page for a new, High Production, farming technology

Brightfield Crate
We need a single landing page, with an email signup for more information.
We build self-contained, farming boxes out of ISO containers. These containers use hydroponics and LED lighting to provide a year round growing environment for crops. So, you could grow crops anywhere at any time of the year in any environment.
For the purpose of this site, we will be doing split testing between several different themes using different sites and keywords.
This site's focus should be providing our product to people searching for high production farming technology.
We'll be focusing on the following key words: Agriculture, aquaponics, farm, garden, hydroponics, organic food, subsistence farming, urban farming, vertical garden.
Target Market(s)
We are going to be using this page to judge that
Number of Pages Required
1 page
Look and feel
Each slider illustrates characteristics of the customer's brand and the style your logo design should communicate.

```html
<!DOCTYPE html>
<html lang="en">
<head>
<meta charset="utf-8">
<title>Brightfield Crate</title>
<link href="https://fonts.googleapis.com/css2?family=Montserrat:wght@400;500;600&family=Open+Sans:ital,wght@0,400;0,600;0,700;1,600&display=swap" rel="stylesheet">
<style>
:root{
  --orange:#e39c5b;
  --green:#97bd7f;
  --ink:#1d1d1d;
  --body:#555;
  --line:#b9b9b9;
  --white:#fff;
}
*{margin:0;padding:0;box-sizing:border-box}
html,body{width:841px;height:1200px;overflow:hidden;background:var(--white);font-family:"Open Sans",sans-serif;color:var(--ink)}
.site-header{height:69px;position:relative;border-bottom:3px solid var(--orange)}
.brand{position:absolute;left:70px;top:22px;display:flex;align-items:center;gap:9px;white-space:nowrap}
.brand-mark{width:22px;height:22px;background:var(--orange)}
.brand-name{font-family:"Montserrat",sans-serif;font-weight:500;font-size:13px;letter-spacing:1.8px;color:var(--green)}
.main-nav{position:absolute;right:68px;top:29px;display:flex;gap:21px;align-items:center;font-family:"Montserrat",sans-serif;font-weight:500;font-size:11.5px;white-space:nowrap}
.main-nav a{color:var(--ink);text-decoration:none}
.main-nav a.active{color:var(--orange)}
.hero{position:relative;height:420px;background:linear-gradient(100deg,#2a5e87 0%,#3c7fae 30%,#5a8fb0 50%,#6aa86a 62%,#3d7aa5 80%,#1f4f77 100%);overflow:hidden}
.hero-copy{position:absolute;left:65px;top:104px;color:var(--white);text-shadow:0 2px 6px rgba(0,0,0,.3);white-space:nowrap}
.hero-kicker{font-family:"Montserrat",sans-serif;font-weight:500;font-size:36px;line-height:1}
.hero-title{font-family:"Montserrat",sans-serif;font-weight:500;font-size:56px;line-height:1.05;margin-top:2px}
.hero-tagline{font-style:italic;font-weight:600;font-size:16px;margin:14px 0 0 5px}
.hero-cta{position:absolute;left:71px;top:250px;width:119px;height:45px;border:2px solid var(--white);border-radius:23px;color:var(--white);font-weight:700;font-size:12px;display:flex;align-items:center;justify-content:center;letter-spacing:.5px}
.slider-dots{position:absolute;left:395px;top:348px;display:flex;gap:3px}
.slider-dots span{width:11px;height:11px;border:1.6px solid var(--white);border-radius:50%}
.slider-dots span.on{background:var(--white)}
.welcome{text-align:center;padding-top:63px}
.welcome h1{font-family:"Montserrat",sans-serif;font-weight:500;font-size:30px;letter-spacing:.5px}
.welcome p{font-size:10px;color:var(--body);line-height:18.5px;margin-top:12px}
.features{display:flex;gap:13px;margin:34px 0 0 69px}
.feature{width:226px;height:202px;border:1px solid var(--line);text-align:center;padding-top:22px}
.feature svg{height:50px}
.feature h2{font-family:"Montserrat",sans-serif;font-weight:500;font-size:13px;letter-spacing:.5px;margin-top:18px}
.feature p{font-size:10px;color:var(--body);line-height:18px;margin-top:10px;padding:0 12px}
.signup{position:absolute;top:929px;left:0;width:841px;height:205px;background:var(--orange);text-align:center;color:var(--white)}
.signup h2{font-family:"Montserrat",sans-serif;font-weight:500;font-size:30px;margin-top:38px;letter-spacing:.5px}
.signup p{font-size:11.5px;margin-top:6px}
.signup-form{display:flex;margin:19px 0 0 178px;width:485px;height:45px}
.signup-input{flex:1;background:var(--white);color:#555;font-size:12px;text-align:left;padding-left:19px;display:flex;align-items:center}
.signup-button{width:104px;background:var(--green);font-weight:700;font-size:12px;display:flex;align-items:center;justify-content:center;letter-spacing:.5px}
.site-footer{position:absolute;top:1160px;width:841px;text-align:center;font-size:9.5px;color:var(--body)}
</style>
</head>
<body>
<header class="site-header">
  <div class="brand"><span class="brand-mark"></span><span class="brand-name">BRIGHTFIELD CRATE</span></div>
  <nav class="main-nav">
    <a class="active" href="#">HOME</a><a href="#">ABOUT US</a><a href="#">SERVICES</a><a href="#">WHY US</a><a href="#">BLOG</a><a href="#">CONTACT US</a>
    <svg width="11" height="11" viewBox="0 0 12 12"><circle cx="5" cy="5" r="3.6" fill="none" stroke="#1d1d1d" stroke-width="1.8"/><path d="M7.6 7.6 11 11" stroke="#1d1d1d" stroke-width="2"/></svg>
  </nav>
</header>
<section class="hero" role="img" aria-label="Interior of a container farm with racks of leafy greens under LED lights">
  <div class="hero-copy">
    <div class="hero-kicker">BRIGHTFIELD</div>
    <div class="hero-title">CRATE</div>
    <div class="hero-tagline">We build self-contained, farming boxes out of ISO containers.</div>
  </div>
  <div class="hero-cta">GET STARTED</div>
  <div class="slider-dots"><span class="on"></span><span></span><span></span><span></span></div>
</section>
<section class="welcome">
  <h1>WELCOME TO BRIGHTFIELD CRATE</h1>
  <p>Nemo enim ipsam voluptatem quia voluptas sit aspernatur aut odit aut fugit, sed quia consequuntur<br>magni dolores eos qui ratione voluptatem sequi nesciun eque porro quisqu</p>
  <div class="features">
    <div class="feature">
      <svg viewBox="0 0 50 50" width="50"><rect x="3" y="7" width="44" height="40" rx="3" fill="#97bd7f"/><rect x="12" y="2" width="4" height="10" rx="2" fill="#97bd7f" stroke="#fff" stroke-width="1.5"/><rect x="34" y="2" width="4" height="10" rx="2" fill="#97bd7f" stroke="#fff" stroke-width="1.5"/><g fill="#fff"><rect x="7" y="18" width="7" height="6"/><rect x="16" y="18" width="8" height="6"/><rect x="26" y="18" width="8" height="6"/><rect x="36" y="18" width="7" height="6"/><rect x="7" y="26" width="7" height="6"/><rect x="16" y="26" width="8" height="6"/><rect x="26" y="26" width="8" height="6"/><rect x="36" y="26" width="7" height="6"/><rect x="7" y="34" width="7" height="8"/><rect x="16" y="34" width="8" height="8"/><rect x="26" y="34" width="8" height="8"/><rect x="36" y="34" width="7" height="8"/></g></svg>
      <h2>YEAR-ROUND GROWING</h2>
      <p>Neque porro quisquam est, qui dolor<br>ipsum quia dolor sit amet, consectetur, adi<br>pisci velit, sed qu uam eius mod</p>
    </div>
    <div class="feature">
      <svg viewBox="0 0 50 50" width="50"><path d="M48 2 2 26l16 4z" fill="#97bd7f"/><path d="M48 2 18 30l6 18z" fill="#83ab6c"/><path d="M48 2 24 48l6-14z" fill="#97bd7f"/></svg>
      <h2>QUICK SETUP</h2>
      <p>Neque porro quisquam est, qui dolor<br>ipsum quia dolor sit amet, consectetur, adi<br>pisci velit, sed qu uam eius mod</p>
    </div>
    <div class="feature">
      <svg viewBox="0 0 50 50" width="50"><circle cx="25" cy="25" r="19" fill="none" stroke="#97bd7f" stroke-width="6"/><path d="M25 14v12h-8" fill="none" stroke="#97bd7f" stroke-width="4"/></svg>
      <h2>REMOTE MONITORING</h2>
      <p>Neque porro quisquam est, qui dolor<br>ipsum quia dolor sit amet, consectetur, adi<br>pisci velit, sed qu uam eius mod</p>
    </div>
  </div>
</section>
<section class="signup">
  <h2>EMAIL SIGNUP</h2>
  <p>Nemo enim ipsam voluptatem quia voluptas sit aspernatur aut oquia conseq</p>
  <div class="signup-form"><div class="signup-input">Email Address</div><div class="signup-button">SIGN UP</div></div>
</section>
<footer class="site-footer">Copyrights © 2018, Brightfield Crate. All Rights Reserved.</footer>
</body>
</html>
```